Home Remodeling company needs a business card design

we need a business card design for home remodeling company in hamilton county, indiana USA. we offers a wide range of construction services including whole house renovations, Design and Build Basements and Kitchen and Bathroom Remodeling . we would like to see designs for both site of business card that use the same color of the company logo and also including all information below :
1- Karim Feltous CEO / General Contractor
2- all company contacts Telephone numbers ( 1-888-DULOM-47 ) ( 317-555-0193) email address ( info@dulomhome.com) website ( www.dulomhome.com ) and social media logos (Facebook- twitter- google plus )
3- company logo
4- licensed . insured . bonded

```html
<!DOCTYPE html>
<html lang="en">
<head>
<meta charset="utf-8">
<title>Dulom Home Remodeling – Business Card</title>
<link rel="stylesheet" href="https://fonts.googleapis.com/css2?family=Open+Sans:wght@400;600;700&display=swap">
<style>
  :root {
    --page-bg: #d9d6d2;
    --card-bg: #0c0c0c;
    --card-edge: #1a1a1a;
    --brand-grey: #8a8a8a;
    --brand-silver: #c9c9c9;
    --brand-red: #d8323b;
    --text-white: #f2f2f2;
  }
  * { margin: 0; padding: 0; box-sizing: border-box; }
  html, body {
    width: 1200px;
    height: 900px;
    overflow: hidden;
    background: var(--page-bg);
    font-family: "Open Sans", Arial, sans-serif;
  }
  .sheet {
    width: 1200px;
    height: 900px;
    display: flex;
    align-items: center;
    justify-content: center;
    gap: 40px;
  }
  .card {
    position: relative;
    width: 540px;
    height: 309px;
    background: var(--card-bg);
    border: 1px solid var(--card-edge);
    box-shadow: 0 10px 28px rgba(0,0,0,0.25);
    color: var(--text-white);
  }

  /* Wordmark */
  .wordmark {
    display: flex;
    align-items: flex-start;
    gap: 10px;
  }
  .wordmark__square {
    width: 12px;
    height: 12px;
    margin-top: 14px;
    background: var(--brand-red);
    flex: none;
  }
  .wordmark__text { display: flex; flex-direction: column; }
  .wordmark__name {
    font-weight: 700;
    font-size: 44px;
    line-height: 1;
    letter-spacing: 2px;
    color: var(--brand-grey);
  }
  .wordmark__tag {
    margin-top: 6px;
    font-weight: 700;
    font-size: 11px;
    letter-spacing: 5.2px;
    color: var(--brand-grey);
  }

  /* Front */
  .card--front .wordmark {
    position: absolute;
    left: 36px;
    top: 110px;
  }
  .contact {
    position: absolute;
    left: 330px;
    top: 58px;
  }
  .contact__name {
    font-weight: 600;
    font-size: 16px;
    color: var(--brand-red);
  }
  .contact__role {
    font-size: 11.5px;
    margin-bottom: 22px;
  }
  .contact__list { list-style: none; }
  .contact__item {
    display: flex;
    align-items: center;
    gap: 8px;
    font-size: 12.5px;
    line-height: 21px;
  }
  .contact__icon { width: 11px; height: 11px; flex: none; }
  .social {
    display: flex;
    gap: 10px;
    margin-top: 20px;
    margin-left: 18px;
  }
  .social__dot {
    width: 18px;
    height: 18px;
    border-radius: 50%;
    background: var(--text-white);
  }

  /* Back */
  .card--back {
    display: flex;
    flex-direction: column;
    align-items: center;
    justify-content: center;
  }
  .card--back .wordmark__name { color: var(--brand-silver); font-size: 50px; }
  .card--back .wordmark__tag { color: var(--brand-silver); letter-spacing: 6.4px; }
  .credentials {
    margin-top: 16px;
    font-size: 13px;
    font-weight: 600;
    color: var(--text-white);
    padding-left: 22px;
  }
</style>
</head>
<body>
<main class="sheet">

  <section class="card card--front" aria-label="Business card front">
    <div class="wordmark">
      <span class="wordmark__square"></span>
      <div class="wordmark__text">
        <span class="wordmark__name">DULOM</span>
        <span class="wordmark__tag">HOME REMODELING</span>
      </div>
    </div>

    <div class="contact">
      <p class="contact__name">Karim Feltous</p>
      <p class="contact__role">CEO / General Contractor</p>
      <ul class="contact__list">
        <li class="contact__item">
          <svg class="contact__icon" viewBox="0 0 12 12"><path fill="#d8323b" d="M2.4 0.6 4.2 2.4 3.2 4a6.5 6.5 0 0 0 4.8 4.8L9.6 7.8l1.8 1.8-1.4 1.9C5 11.2 0.8 7 0.5 2z"/></svg>
          1-888-DULOM-47
        </li>
        <li class="contact__item">
          <svg class="contact__icon" viewBox="0 0 12 12"><path fill="#d8323b" d="M2.4 0.6 4.2 2.4 3.2 4a6.5 6.5 0 0 0 4.8 4.8L9.6 7.8l1.8 1.8-1.4 1.9C5 11.2 0.8 7 0.5 2z"/></svg>
          317-555-0193
        </li>
        <li class="contact__item">
          <svg class="contact__icon" viewBox="0 0 12 12"><rect x="0.5" y="2" width="11" height="8" fill="#d8323b"/><path d="M0.8 2.4 6 6.6l5.2-4.2" fill="none" stroke="#0c0c0c" stroke-width="1"/></svg>
          info@dulomhome.com
        </li>
        <li class="contact__item">
          <svg class="contact__icon" viewBox="0 0 12 12"><g fill="none" stroke="#d8323b" stroke-width="1.6"><rect x="1" y="5" width="6" height="3.4" rx="1.7" transform="rotate(-45 4 6.7)"/><rect x="5" y="3.6" width="6" height="3.4" rx="1.7" transform="rotate(-45 8 5.3)"/></g></svg>
          www.dulomhome.com
        </li>
      </ul>
      <div class="social" aria-label="Social media">
        <span class="social__dot"></span>
        <span class="social__dot"></span>
        <span class="social__dot"></span>
      </div>
    </div>
  </section>

  <section class="card card--back" aria-label="Business card back">
    <div class="wordmark">
      <span class="wordmark__square"></span>
      <div class="wordmark__text">
        <span class="wordmark__name">DULOM</span>
        <span class="wordmark__tag">HOME REMODELING</span>
      </div>
    </div>
    <p class="credentials">Licensed . Insured . Bonded</p>
  </section>

</main>
</body>
</html>
```